Business Card Design - Amberfield Court

We are looking at a new design for our business cards that has a modern and professional look. We run a residential aged care facility focussing on the care of residents. The cards will be used for potential clients, consultants and business opportunities in this sector. Blue and white is our main colours and would to see these colours incorporated in the design.
Industry/Entity Type
Business
Contact Information for Business Card
Amberfield Court, Darren Walsh, dwalsh@amberfieldcourt.com.au, Finance Manager, 0472 639 208, BCom, 37 Marrabel Crescent, Brindle Vale, Qld 4093.
Look and feel
Each slider illustrates characteristics of the customer's brand and the style your logo design should communicate.

```html
<!DOCTYPE html>
<html lang="en">
<head>
<meta charset="UTF-8">
<title>Amberfield Court – Business Card</title>
<link rel="stylesheet" href="https://fonts.googleapis.com/css2?family=Open+Sans:wght@400;600;700;800&display=swap">
<style>
  :root {
    --navy: #1f3d4f;
    --steel: #4a7b98;
    --taupe: #b3a59b;
    --ink: #1d3447;
    --paper: #ffffff;
    --backdrop: #e6e8ea;
  }
  * { margin: 0; padding: 0; box-sizing: border-box; }
  html, body { width: 1200px; height: 900px; overflow: hidden; }
  body {
    background: var(--backdrop);
    font-family: "Open Sans", Arial, sans-serif;
    position: relative;
  }
  .card {
    position: absolute;
    width: 520px;
    height: 300px;
    border-radius: 22px;
    box-shadow: 0 10px 28px rgba(0,0,0,0.18);
    overflow: hidden;
  }
  .card-front {
    left: 70px; top: 140px;
    background: var(--navy);
    display: flex; align-items: center; justify-content: center;
  }
  .card-back {
    left: 610px; top: 460px;
    background: var(--paper);
  }
  .brand {
    display: flex; align-items: center; gap: 12px;
    color: var(--paper);
    font-weight: 600;
    letter-spacing: 0.08em;
    text-transform: uppercase;
  }
  .brand-dot {
    width: 18px; height: 18px; border-radius: 50%;
    background: var(--steel);
  }
  .card-front .brand { font-size: 30px; }
  .card-back .brand {
    position: absolute; right: 34px; top: 44px;
    color: var(--steel);
    font-size: 19px;
  }
  .card-back .brand-dot { width: 13px; height: 13px; }
  .address {
    position: absolute; right: 34px; top: 150px;
    text-align: right;
    font-size: 13px; line-height: 1.4;
    color: var(--ink);
  }
  .divider {
    position: absolute; left: 34px; right: 34px; top: 196px;
    height: 1.5px; background: var(--steel);
  }
  .person {
    position: absolute; left: 34px; top: 166px;
    font-size: 22px; font-weight: 800;
    color: var(--ink);
    letter-spacing: 0.01em;
  }
  .role {
    position: absolute; left: 34px; top: 201px;
    font-size: 12px; color: var(--steel);
    letter-spacing: 0.02em;
  }
  .contacts {
    position: absolute; left: 34px; top: 226px;
    list-style: none;
    font-size: 14px; color: var(--ink);
    line-height: 1.55;
  }
  .contacts li { display: flex; align-items: center; gap: 8px; }
  .contacts svg { width: 12px; height: 12px; fill: none; stroke: var(--steel); stroke-width: 2; }
</style>
</head>
<body>
  <section class="card card-front">
    <div class="brand"><span class="brand-dot"></span>Amberfield Court</div>
  </section>

  <section class="card card-back">
    <div class="brand"><span class="brand-dot"></span>Amberfield Court</div>
    <p class="address">37 Marrabel Crescent<br>Brindle Vale, Qld 4093</p>
    <h1 class="person">DARREN WALSH</h1>
    <div class="divider"></div>
    <p class="role">FINANCE MANAGER(BCOM)</p>
    <ul class="contacts">
      <li>
        <svg viewBox="0 0 24 24"><path d="M5 3h4l2 5-3 2a12 12 0 0 0 6 6l2-3 5 2v4a2 2 0 0 1-2 2A17 17 0 0 1 3 5a2 2 0 0 1 2-2z"/></svg>
        0472 639 208
      </li>
      <li>
        <svg viewBox="0 0 24 24"><rect x="2" y="5" width="20" height="14" rx="1"/><path d="M2 6l10 7 10-7"/></svg>
        dwalsh@amberfieldcourt.com.au
      </li>
    </ul>
  </section>
</body>
</html>
```